Harborline Auto LLC

Car Dealer Customer Service
Address: 2874 Cresthaven Road, Shelbyville, TN 37162
web: www.harborlineautoxq.net
email: harborlineautoxq@mailnest.example
Phone: (931) 555-0148
Phone: (629) 555-0173

```html
<!DOCTYPE html>
<html lang="en">
<head>
<meta charset="utf-8">
<title>Harborline Auto LLC — Business Card</title>
<link href="https://fonts.googleapis.com/css2?family=Lexend:wght@400;500&display=swap" rel="stylesheet">
<style>
  :root{
    --paper:#ffffff;
    --ink:#464646;
    --brand-blue:#2a8fc6;
    --icon-blue:#29abe2;
    --bar-blue:#118fcf;
    --brand-gold:#ebb146;
  }
  html,body{margin:0;padding:0;overflow:hidden;background:var(--paper);}
  .card{
    position:relative;width:1200px;height:1200px;background:var(--paper);
    font-family:"Lexend",sans-serif;color:var(--ink);overflow:hidden;
  }
  .brand-mark{
    position:absolute;left:-40px;top:470px;width:300px;height:300px;
    border-radius:50%;background:var(--brand-blue);
  }
  .brand-name{
    position:absolute;left:290px;top:560px;margin:0;
    font-size:44px;font-weight:500;line-height:1.15;color:var(--brand-gold);
  }
  .person{position:absolute;left:646px;top:492px;margin:0;}
  .person-name,.person-title{
    display:block;font-size:42px;font-weight:500;line-height:42px;letter-spacing:0.5px;
  }
  .contact-list{list-style:none;margin:0;padding:0;}
  .contact-item{position:absolute;left:644px;display:flex;align-items:flex-start;}
  .contact-icon{width:40px;height:37px;flex:none;}
  .contact-text{
    position:absolute;left:58px;top:-6px;white-space:nowrap;
    font-size:30px;line-height:37px;font-weight:400;
  }
  .contact-text.email{font-size:26px;top:-2px;}
  .item-address{top:598px;}
  .item-email{top:684px;}
  .item-phone{top:735px;}
  .rule{position:absolute;top:852px;height:16px;}
  .rule-blue{left:9px;width:793px;background:var(--bar-blue);}
  .rule-gold{left:802px;width:391px;background:var(--brand-gold);}
</style>
</head>
<body>
<div class="card">
  <div class="brand-mark"></div>
  <p class="brand-name">Harborline<br>Auto LLC</p>

  <div class="rule rule-blue"></div>
  <div class="rule rule-gold"></div>

  <h1 class="person">
    <span class="person-name">YOUR NAME NAME</span>
    <span class="person-title">XXXXXXXX</span>
  </h1>

  <ul class="contact-list">
    <li class="contact-item item-address">
      <svg class="contact-icon" viewBox="0 0 40 37" aria-hidden="true">
        <rect width="40" height="37" fill="var(--icon-blue)"/>
        <path d="M20 6 L33 19 H30 V31 H24 V24 H16 V31 H10 V19 H7 Z" fill="#fff"/>
      </svg>
      <span class="contact-text">2874 Cresthaven Road,<br>Shelbyville, TN 37162</span>
    </li>
    <li class="contact-item item-email">
      <svg class="contact-icon" viewBox="0 0 40 37" aria-hidden="true">
        <rect width="40" height="37" fill="var(--icon-blue)"/>
        <rect x="8" y="9" width="24" height="19" fill="none" stroke="#fff" stroke-width="2"/>
        <path d="M8 9 L20 20 L32 9 M8 28 L17 18 M32 28 L23 18" fill="none" stroke="#fff" stroke-width="2"/>
      </svg>
      <span class="contact-text email">harborlineautoxq@mailnest.example</span>
    </li>
    <li class="contact-item item-phone">
      <svg class="contact-icon" viewBox="0 0 40 37" aria-hidden="true">
        <rect width="40" height="37" fill="var(--icon-blue)"/>
        <path d="M25 8 C21 9 17 16 18 25 C18 29 21 30 22 28 C23 26 21 25 20 25 C20 20 22 16 24 14 C25 15 27 15 28 12 C28 10 26 8 25 8 Z" fill="#fff"/>
      </svg>
      <span class="contact-text">(931) 555-0148<br>(629) 555-0173</span>
    </li>
  </ul>
</div>
</body>
</html>
```